Brightmill Data Works

Our company is about IT hardwares and IT solutions. IT hardware such as PC, RAMS, storage and servers. IT solutions such as project management, BA. We are also selling new technology too.

Target Market(s)

Consumer, Small to Medium Business, Corporate

Requirements
Must have
• The business card must have the following:
• Name:
• Title:
• Contact Number:
• Email address:
• Website:
• Color: Must match the logo color upgrade

```html
<!DOCTYPE html>
<html lang="en">
<head>
<meta charset="utf-8">
<title>Brightmill Data Works — Business Card</title>
<link href="https://fonts.googleapis.com/css2?family=Saira:wght@400;500;600;800&display=swap" rel="stylesheet">
<style>
  :root {
    --bg: #e4e4e4;
    --card: #f7f7f7;
    --orange-light: #e2a553;
    --orange-dark: #c96f2a;
    --charcoal: #505050;
    --ink: #1c1c1c;
    --wordmark: #555555;
    --white: #ffffff;
  }
  * { box-sizing: border-box; margin: 0; padding: 0; }
  html, body {
    width: 1200px; height: 864px; overflow: hidden;
    background: var(--bg);
    font-family: "Saira", sans-serif;
  }
  .stage { position: relative; width: 1200px; height: 864px; }
  .card {
    position: absolute;
    width: 540px; height: 309px;
    background: var(--card);
    box-shadow: 0 10px 28px rgba(0,0,0,.18);
    overflow: hidden;
  }
  .card svg.swoosh { position: absolute; inset: 0; width: 100%; height: 100%; }
  .card--back { left: 620px; top: 110px; }
  .card--front { left: 40px; top: 440px; }

  .brand {
    position: absolute;
    display: flex; align-items: center; gap: 12px;
  }
  .brand__mark {
    width: 18px; height: 18px;
    background: var(--orange-dark);
    flex: none;
  }
  .brand__name {
    font-weight: 800;
    color: var(--wordmark);
    line-height: 1.05;
    text-transform: uppercase;
    letter-spacing: .5px;
  }
  .card--back .brand { left: 80px; top: 48px; }
  .card--back .brand__name { font-size: 28px; }
  .card--front .brand { left: 258px; top: 88px; }
  .card--front .brand__name { font-size: 25px; }

  .holder { position: absolute; left: 22px; top: 150px; }
  .holder__name {
    font-weight: 600; font-size: 21px; color: var(--ink);
    text-transform: uppercase; letter-spacing: .5px; line-height: 1.1;
  }
  .holder__title {
    font-weight: 400; font-size: 17px; color: var(--white);
    text-transform: uppercase; line-height: 1.1;
  }

  .contacts {
    position: absolute; right: 22px; top: 178px;
    list-style: none;
    display: flex; flex-direction: column; gap: 5px;
  }
  .contacts li {
    display: flex; align-items: center; justify-content: flex-end; gap: 8px;
    font-size: 15px; font-weight: 500; color: var(--ink); letter-spacing: 1px;
  }
  .contacts .icon {
    width: 20px; height: 20px; background: var(--orange-dark);
    display: flex; align-items: center; justify-content: center; flex: none;
  }
  .contacts .icon svg { width: 14px; height: 14px; }
</style>
</head>
<body>
<main class="stage">

  <section class="card card--back" aria-label="Card back">
    <svg class="swoosh" viewBox="0 0 540 309" preserveAspectRatio="none" aria-hidden="true">
      <defs>
        <linearGradient id="orangeBack" x1="0" y1="0" x2="1" y2="0">
          <stop offset="0" stop-color="#e2a553"/>
          <stop offset="1" stop-color="#c96f2a"/>
        </linearGradient>
      </defs>
      <path d="M0,215 C230,205 380,150 480,0 L540,0 L540,55 C400,130 230,190 0,225 Z" fill="#505050"/>
      <path d="M0,225 C230,190 400,130 540,55 L540,309 L0,309 Z" fill="url(#orangeBack)"/>
    </svg>
    <div class="brand">
      <span class="brand__mark"></span>
      <span class="brand__name">Brightmill<br>Data Works</span>
    </div>
  </section>

  <section class="card card--front" aria-label="Card front">
    <svg class="swoosh" viewBox="0 0 540 309" preserveAspectRatio="none" aria-hidden="true">
      <defs>
        <linearGradient id="orangeFront" x1="0" y1="0" x2="1" y2="1">
          <stop offset="0" stop-color="#e2a553"/>
          <stop offset="1" stop-color="#d5893a"/>
        </linearGradient>
      </defs>
      <path d="M150,0 L220,0 C185,120 330,255 470,309 L440,309 C300,270 170,150 150,0 Z" fill="#505050"/>
      <path d="M0,0 L150,0 C165,150 300,265 440,309 L0,309 Z" fill="url(#orangeFront)"/>
    </svg>

    <div class="holder">
      <p class="holder__name">Nora Vale</p>
      <p class="holder__title">Manager</p>
    </div>

    <div class="brand">
      <span class="brand__mark"></span>
      <span class="brand__name">Brightmill<br>Data Works</span>
    </div>

    <ul class="contacts">
      <li>+1-555-014-2290
        <span class="icon"><svg viewBox="0 0 24 24" aria-hidden="true"><path d="M6.6 10.8a15 15 0 0 0 6.6 6.6l2.2-2.2a1 1 0 0 1 1-.25 11.4 11.4 0 0 0 3.6.57 1 1 0 0 1 1 1V20a1 1 0 0 1-1 1A17 17 0 0 1 3 4a1 1 0 0 1 1-1h3.5a1 1 0 0 1 1 1c0 1.25.2 2.45.57 3.57a1 1 0 0 1-.25 1z" fill="#fff"/></svg></span>
      </li>
      <li>nora@brightmilldata.com
        <span class="icon"><svg viewBox="0 0 24 24" aria-hidden="true"><rect x="3" y="6" width="18" height="12" fill="none" stroke="#fff" stroke-width="2"/><path d="M3 6l9 7 9-7" fill="none" stroke="#fff" stroke-width="2"/></svg></span>
      </li>
      <li>www.brightmilldata.com
        <span class="icon"><svg viewBox="0 0 24 24" aria-hidden="true"><g fill="none" stroke="#fff" stroke-width="1.8"><circle cx="12" cy="12" r="9"/><ellipse cx="12" cy="12" rx="4" ry="9"/><path d="M3 12h18M5 7h14M5 17h14"/></g></svg></span>
      </li>
    </ul>
  </section>

</main>
</body>
</html>
```